Website for a company offering full serivce charging solutions for electric cars

The company "tanu-werk" (english: "tanu-works") offering all-in-one-solutions for charging infrastructure for electric mobility.

There are four products:
1- Wallboxes for single-family homes
2- Solutions for property devloper/-management for property parking space
3- All-in-one-charging solution for municipalities/communities
4- Solutions for tourism/hotels/holiday appartments

The Website structure:
1. Main Page
2.1. Product Page Single Homes
2.2. Product Page Property Management / Parking
2.3. Product Page Municipality
2.4. Product Page Tourism
3. Contact Form / Request for information
4. Imprint / Legal

The Website should be built on Wordpress with a powerful possibility to simply add/modify specific landing pages.

We would like you to implement the website later and also maintain it if possible, but we would be able to do minor modifications by ourselfs (for A/B-Testing)

The website should be clear and simple, easy to understand.
Target group is mainly B2C without deeper knowledge of that topic.

It should suggest, that we will provide a very simple way to get the charging infrastructure done.

We need a contact form, maybe we will use Hubspot later.

Attached you will find a draft of the main page and a landing page (for 2.2) - it is just the content, please ignore the design. We would love to let you create a suitable design.
Also you will find some drafts a bit different for the same story.

I added also a few stock photos, but they don't need to be used! If you have better ideas, you are welcome!

Industry/Entity Type

Charging/Electric mobility

Number of Pages Required

2 page

Font styles to use
Sans Serif

Requirements
Must have
• Based on Wordpress, and the designer should be able to implement it on Wordpress on a later step

```html
<!DOCTYPE html>
<html lang="de">
<head>
<meta charset="utf-8">
<title>tanu-werk – einfach mehr als laden</title>
<link rel="stylesheet" href="https://fonts.googleapis.com/css2?family=Titillium+Web:wght@300;400;600;700&family=Montserrat:wght@500;600&family=Arimo:wght@400;700&display=swap">
<style>
:root{
  --bg:#121a29;
  --bg-deep:#0d1320;
  --pink:#e3158f;
  --purple:#7d5bc6;
  --violet:#5b2a9a;
  --text:#ffffff;
  --muted:#c9cbd6;
  --line:#2a3347;
}
*{margin:0;padding:0;box-sizing:border-box}
html,body{width:1200px;height:4161px;overflow:hidden;background:var(--bg);color:var(--text);font-family:"Arimo",Arial,sans-serif}
.page{position:relative;width:1200px;height:4161px;overflow:hidden}
.abs{position:absolute}

/* header */
.site-header{position:absolute;left:0;top:0;width:1200px;height:81px;background:var(--bg)}
.brand{position:absolute;left:104px;top:16px;display:flex;align-items:center;gap:12px}
.brand-dot{width:34px;height:34px;border-radius:50%;border:3px solid var(--pink)}
.brand-name{font-family:"Titillium Web",sans-serif;font-size:25px;font-weight:600;line-height:24px;color:var(--text)}
.brand-tag{font-size:13px;color:var(--text);line-height:16px}
.nav a{position:absolute;top:30px;font-size:16px;color:var(--text);text-decoration:none;transform:translateX(-50%)}
.nav .cta{top:23px;left:966px;width:124px;height:38px;transform:none;border-radius:19px;background:linear-gradient(90deg,var(--purple),var(--pink));font-weight:700;display:flex;align-items:center;justify-content:center;box-shadow:0 0 10px rgba(227,21,143,.6)}

/* hero */
.hero-media{position:absolute;left:0;top:81px;width:1200px;height:594px;border-bottom-right-radius:150px;background:linear-gradient(100deg,#d62aa7 0%,#b43fc9 35%,#7b36c9 60%,#3a2ca6 85%,#1c2a8a 100%)}
.hero-title{position:absolute;left:108px;top:262px;font-family:"Titillium Web",sans-serif;font-size:52px;line-height:54px;color:var(--text)}
.hero-title b{font-weight:700;display:block}
.hero-title span{font-weight:300;display:block}
.hero-lead{position:absolute;left:110px;top:388px;width:450px;font-size:19px;line-height:31px;font-weight:400}

/* intro */
.intro-heading{position:absolute;left:180px;top:734px;width:840px;text-align:center;font-family:"Montserrat",sans-serif;font-weight:500;font-size:22px;line-height:26px}
.intro-copy{position:absolute;left:200px;top:842px;width:800px;text-align:center;font-size:15px;line-height:26px;color:#e6e7ee}
.intro-media{position:absolute;left:150px;top:955px;width:840px;height:280px;border-radius:10px;background:radial-gradient(ellipse at 50% 70%,rgba(80,220,230,.55),rgba(70,60,190,.35) 45%,rgba(18,26,41,0) 75%)}
.ask{position:absolute;left:250px;top:1264px;width:700px;text-align:center;font-family:"Titillium Web",sans-serif;font-weight:600;font-size:28px;line-height:35px}

/* grid backdrop bands */
.grid-band{position:absolute;left:0;width:1200px;background:linear-gradient(180deg,rgba(18,26,41,0),rgba(120,40,140,.28) 50%,rgba(18,26,41,0))}

/* segments */
.seg-title{position:absolute;font-family:"Titillium Web",sans-serif;font-weight:600;font-size:38px;line-height:44px}
.seg-title.pink{color:var(--pink)}
.seg-title.purple{color:var(--purple)}
.plain-list{position:absolute;list-style:none;font-size:13.5px;line-height:18px;color:#e8e9ef}
.plain-list li{margin-bottom:9px}
.chev-list{position:absolute;list-style:none;font-size:13.5px;line-height:18px;color:#e8e9ef}
.chev-list li{position:relative;padding-left:22px;margin-bottom:9px}
.chev-list li::before{content:"";position:absolute;left:3px;top:5px;width:6px;height:6px;border-right:2px solid var(--pink);border-bottom:2px solid var(--pink);transform:rotate(-45deg)}
.chev-list .sub{list-style:none;padding-left:22px;margin-top:8px}
.chev-list .sub li{padding-left:0;margin-bottom:1px}
.chev-list .sub li::before{display:none}

/* contact */
.contact{position:absolute;left:0;top:3206px;width:1200px;height:590px;background:linear-gradient(90deg,#d60fb6 0%,#b62bc4 35%,#8a3bd0 60%,#6a48c8 100%)}
.contact-media{position:absolute;left:640px;top:0;width:560px;height:590px;background:linear-gradient(180deg,rgba(190,170,230,.35),rgba(90,90,220,.45));}
.contact h2{position:absolute;left:113px;top:90px;font-family:"Titillium Web",sans-serif;font-size:40px;line-height:44px;font-weight:400}
.contact h2 b{font-weight:700}
.contact h2::after{content:"";position:absolute;left:0;top:48px;width:58px;height:4px;background:#fff}
.contact-lead{position:absolute;left:116px;top:154px;width:470px;font-size:15px;line-height:20px}
.field{position:absolute;background:#fff;color:#666;font-size:12px;padding:14px 16px 0}
.submit{position:absolute;left:126px;top:428px;width:181px;height:50px;border:2px solid #fff;border-radius:4px;display:flex;align-items:center;justify-content:center;font-weight:700;font-size:16px}

/* footer */
.site-footer{position:absolute;left:0;top:3796px;width:1200px;height:298px;background:var(--bg)}
.foot-brand{position:absolute;left:110px;top:112px;display:flex;align-items:center;gap:12px}
.foot-brand .brand-dot{width:40px;height:40px}
.foot-brand .brand-name{font-size:36px;line-height:40px}
.foot-div{position:absolute;top:0;width:1px;height:298px;background:var(--line)}
.foot-col{position:absolute;top:80px}
.foot-col h3{font-family:"Montserrat",sans-serif;font-weight:600;font-size:17px;border-left:3px solid var(--pink);padding-left:22px;line-height:22px;margin-left:-26px;margin-bottom:14px}
.foot-col a{display:block;color:#a9adbb;text-decoration:none;font-size:15px;line-height:31px}
.social{display:flex;gap:8px;margin-top:2px}
.social span{width:33px;height:33px;border-radius:50%;background:var(--pink)}
.copyright{position:absolute;left:0;top:4094px;width:1200px;height:67px;background:var(--bg-deep);display:flex;align-items:center;justify-content:center;font-size:14px;color:#d0d2db}
</style>
</head>
<body>
<div class="page">

  <header class="site-header">
    <div class="brand">
      <span class="brand-dot"></span>
      <div>
        <div class="brand-name">tanu-werk.de</div>
        <div class="brand-tag">einfach mehr als laden</div>
      </div>
    </div>
    <nav class="nav">
      <a style="left:491px" href="#">Lösungen</a>
      <a style="left:636px" href="#">Unternehmen</a>
      <a style="left:775px" href="#">Services</a>
      <a style="left:893px" href="#">Karriere</a>
      <a class="cta" href="#">Kontakt</a>
    </nav>
  </header>

  <section>
    <div class="hero-media" role="img" aria-label="Nahaufnahme eines Ladesteckers an einer Ladesäule in pink-violettem Licht"></div>
    <h1 class="hero-title"><b>TANU-WERK IST</b><span>IHR PARTNER</span></h1>
    <p class="hero-lead">wenn das Laden nicht nur einfach, sondern die Umsetzung auch aus einer Hand kommen soll</p>
  </section>

  <section>
    <h2 class="intro-heading">Wir&nbsp; bieten Lösungen sowohl für Privatkunden, Geschäftskunden als auch Kommunen an, die schnell, fair und ohne Eigenleistung zu einer smarten Ladelösung für E-Fahrzeuge kommen möchten.</h2>
    <p class="intro-copy">Von der Beratung, über die Installation, Inbetriebnahme bis zur Abrechnung und Wartung bekommen Sie bei tanu-werk alles aus einer Hand. Auf Wunsch vermieten wir auch die Ladetechnik und übernehmen im gewerblichen Bereich die direkte Abrechnung mit dem Nutzer. Für Kommunen bieten wir den kostenfreien Full-Service an und beteiligen die Gemeinden an der Nutzung der Infrastruktur.</p>
    <div class="intro-media" role="img" aria-label="Leuchtende Illustration eines Elektroautos an Ladesäulen mit Akkuanzeige"></div>
    <h2 class="ask">Fragen Sie uns nach der auf Ihre individuellen Bedürfnisse zugeschnittenen Lösung:</h2>
  </section>

  <div class="grid-band" style="top:1780px;height:170px"></div>
  <div class="grid-band" style="top:2440px;height:200px"></div>
  <div class="grid-band" style="top:3000px;height:200px"></div>

  <!-- connectors and medallions -->
  <svg class="abs" style="left:0;top:1380px" width="1200" height="1800" viewBox="0 1380 1200 1800">
    <defs>
      <radialGradient id="halo" cx="50%" cy="50%" r="50%">
        <stop offset="70%" stop-color="#3a1e5c"/>
        <stop offset="100%" stop-color="#241833"/>
      </radialGradient>
      <linearGradient id="ph1" x1="0" y1="0" x2="1" y2="1"><stop offset="0" stop-color="#e9ecf2"/><stop offset=".5" stop-color="#3a6df0"/><stop offset="1" stop-color="#c9ced8"/></linearGradient>
      <linearGradient id="ph2" x1="0" y1="0" x2="1" y2="1"><stop offset="0" stop-color="#dfe7f2"/><stop offset=".5" stop-color="#8fa9c8"/><stop offset="1" stop-color="#2f5f9c"/></linearGradient>
      <linearGradient id="ph3" x1="0" y1="0" x2="1" y2="1"><stop offset="0" stop-color="#cfe0f6"/><stop offset=".5" stop-color="#2a6be8"/><stop offset="1" stop-color="#1a2c7a"/></linearGradient>
    </defs>
    <g fill="none" stroke="var(--pink)" stroke-width="2" opacity=".8">
      <path d="M428 1790 V1860 Q428 1878 446 1878 H830 Q848 1878 848 1896 V1985"/>
      <path d="M848 2430 V2500 Q848 2518 830 2518 H446 Q428 2518 428 2536 V2600"/>
    </g>
    <g fill="none" stroke="var(--purple)" stroke-width="3" stroke-linecap="round">
      <path d="M836 1985 h24 v10 a12 12 0 0 1 -24 0 z M842 1978 v7 M854 1978 v7 M848 2007 v10"/>
      <path d="M416 2600 h24 v10 a12 12 0 0 1 -24 0 z M422 2593 v7 M434 2593 v7 M428 2622 v10"/>
    </g>
    <g>
      <circle cx="331" cy="1615" r="226" fill="url(#halo)"/>
      <circle cx="331" cy="1615" r="194" fill="none" stroke="var(--pink)" stroke-width="2"/>
      <circle cx="331" cy="1615" r="182" fill="#2a1840"/>
      <circle cx="331" cy="1615" r="178" fill="url(#ph1)" role="img" aria-label="Weißer Ladestecker in einer blau leuchtenden Ladebuchse"/>
    </g>
    <g>
      <circle cx="848" cy="2229" r="226" fill="url(#halo)"/>
      <circle cx="848" cy="2229" r="194" fill="none" stroke="var(--pink)" stroke-width="2"/>
      <circle cx="848" cy="2229" r="182" fill="#2a1840"/>
      <circle cx="848" cy="2229" r="178" fill="url(#ph2)" role="img" aria-label="Ladestecker mit orangem Licht am Elektroauto"/>
    </g>
    <g>
      <circle cx="331" cy="2867" r="226" fill="url(#halo)"/>
      <circle cx="331" cy="2867" r="194" fill="none" stroke="var(--pink)" stroke-width="2"/>
      <circle cx="331" cy="2867" r="182" fill="#2a1840"/>
      <circle cx="331" cy="2867" r="178" fill="url(#ph3)" role="img" aria-label="Elektroauto lädt an blau leuchtender Ladesäule"/>
    </g>
  </svg>

  <section>
    <h2 class="seg-title pink" style="left:598px;top:1450px">als Privatkunde</h2>
    <ul class="plain-list" style="left:599px;top:1522px;width:500px">
      <li>Bestandsanalyse mit umfangreicher Beratung über die Möglichkeiten der Umsetzung</li>
      <li>Prüfung und Übernahme der Anmeldung verfügbarer Fördermöglichkeiten</li>
      <li>Auswahl an smarten Wallbox Lösungen, passend für Ihr Fahrzeug und Ihre Bedürfnisse</li>
      <li>Installation inkl. aller notwendigen Materialien und Tätigkeiten (Durchbrüche, Erdarbeiten, etc.)</li>
      <li>Inbetriebnahme und Einweisung in die Ladetechnik</li>
      <li>Jährlich technische Wartung nach DGUV3</li>
      <li>Reparaturservice, unter Berücksichtigung der geltenden Garantie Ansprüche</li>
    </ul>
  </section>

  <section>
    <h2 class="seg-title purple" style="left:125px;top:1962px">als Geschäftskunde</h2>
    <ul class="chev-list" style="left:130px;top:2031px;width:520px">
      <li>Durchführung einer individuellen Bedarfsanalyse inkl. Ermittlung der Anforderungen für:
        <ul class="sub">
          <li>Haus- und Immobilienverwaltungen</li>
          <li>Dienstleistungs- und Handelsunternehmen</li>
          <li>Hotel und Beherbergungsbetriebe</li>
          <li>Parkraum- und Parkhausbetreiber</li>
          <li>Tourismus, Sport- und Freizeiteinrichtungen</li>
        </ul>
      </li>
      <li style="margin-top:20px">Planung und Projektierung des Installationsaufwands inkl. Materialverbrauch</li>
      <li>Leasing oder Kauf der Hardware</li>
      <li>Normgerechte Installation der Ladeinfrastruktur inkl. Durchbruch-, Brandschutz- und Erdarbeiten</li>
      <li>Bei Bestandsbauten Integration der Ladeinfrastruktur in die Gebäudesystemtechnik und ggf. Anpassung des Netzanschlusses</li>
      <li>Inbetriebnahme der Anlage inkl. Prüf- und Messprotokollen</li>
      <li>Wiederkehrende technische Prüfung der Anlage nach DGUV 3</li>
      <li>Austausch und Reparatur Service</li>
      <li>Unterstützung bei der mtl. Nutzungsabrechnung und Einbindung in Ihre vorhandene Abrechnungssysteme</li>
      <li>ODER direkte Abrechnung mit den Nutzern</li>
    </ul>
  </section>

  <section>
    <h2 class="seg-title pink" style="left:604px;top:2674px">als Kommune</h2>
    <ul class="chev-list" style="left:604px;top:2738px;width:520px">
      <li>Konzeptionierung möglicher Ladeinfrastrukturen innerhalb Ihrer Gemeinde</li>
      <li>Planung und Projektsteuerung inkl. sämtlicher behördlicher Genehmigungsverfahren und Beantragung von Fördermitteln</li>
      <li>Fachgerechte Installation und Inbetriebnahme</li>
      <li>Regelmäßige Wartung gemäß Vorschrift</li>
      <li>Reparatur und Kundenservice</li>
      <li>Direkte Abrechnung mit dem Nutzer</li>
      <li>Beteiligung der Gemeinde am Umsatz</li>
      <li>Möglichkeit der Integration von Bonusprogrammen, mit denen der lokale Einzelhandel beworben wird</li>
    </ul>
  </section>

  <section class="contact">
    <div class="contact-media" role="img" aria-label="Weißes Elektroauto an einer Wandladestation"></div>
    <h2><b>CONTACT</b> US</h2>
    <p class="contact-lead">Lorem ipsum dolor sit amet, consectetur adipiscing elit, sed do eiusmod tempor incididunt ut labore et dolore magna aliqua.</p>
    <div class="field" style="left:116px;top:218px;width:236px;height:41px">First Name</div>
    <div class="field" style="left:358px;top:218px;width:238px;height:41px">Last Name</div>
    <div class="field" style="left:116px;top:270px;width:236px;height:41px">Email address</div>
    <div class="field" style="left:358px;top:270px;width:238px;height:41px">Phone number</div>
    <div class="field" style="left:116px;top:323px;width:480px;height:89px">Message</div>
    <div class="submit">SUBMIT NOW</div>
  </section>

  <footer class="site-footer">
    <div class="foot-brand"><span class="brand-dot"></span><span class="brand-name">tanu-werk.de</span></div>
    <div class="foot-div" style="left:392px"></div>
    <div class="foot-div" style="left:651px"></div>
    <div class="foot-div" style="left:867px"></div>
    <div class="foot-col" style="left:420px">
      <h3>NAVIGATION</h3>
      <a href="#">AGB</a><a href="#">Datenschutzerklärung</a><a href="#">Impressum</a>
    </div>
    <div class="foot-col" style="left:676px">
      <h3>RESOURCES</h3>
      <a href="#">Kontakt</a><a href="#">Karriere</a><a href="#">FAQs</a>
    </div>
    <div class="foot-col" style="left:888px">
      <h3>FOLLOW US</h3>
      <div class="social"><span aria-label="Social 1"></span><span aria-label="Social 2"></span><span aria-label="Social 3"></span><span aria-label="Social 4"></span></div>
    </div>
  </footer>
  <div class="copyright">© 2022 tanu-werk GmbH</div>

</div>
</body>
</html>
```